RTavenor Business Cards & Letterhead

I have a logo but need a design for some new business cards. We are a Design-Build Firm that specializes in the design and construction of commercial projects.
the cards need to be professional. no cartoon stuff.
i would like to have the cards in AI format so I can update the card as needed. Logo is provided.
Our Address is: 4187 Marlowe Ct. Linden Falls, Westmoor County 27614

```html
<!DOCTYPE html>
<html lang="en">
<head>
<meta charset="utf-8">
<title>RTavenor Business Card</title>
<link href="https://fonts.googleapis.com/css2?family=Open+Sans:wght@400;600;700&display=swap" rel="stylesheet">
<style>
  :root {
    --backdrop: #0d0d0f;
    --card: #212125;
    --blue: #1672b8;
    --blue-deep: #0c3d6a;
    --blue-light: #1a86d0;
    --wordmark-grey: #66666b;
    --text-light: #eeeef0;
  }
  * { margin: 0; padding: 0; box-sizing: border-box; }
  html, body {
    width: 1200px; height: 780px; overflow: hidden;
    background: var(--backdrop);
    font-family: "Open Sans", Arial, sans-serif;
  }
  .canvas { position: relative; width: 1200px; height: 780px; }
  .card {
    position: absolute; top: 217px;
    width: 570px; height: 345px;
    background: var(--card);
    overflow: hidden;
  }
  .card--back { left: 20px; }
  .card--front { left: 610px; }

  .mark-square {
    position: absolute; top: 22px;
    width: 300px; height: 300px;
    background: linear-gradient(135deg, var(--blue-light) 0%, var(--blue) 45%, var(--blue-deep) 100%);
  }
  .card--back .mark-square { left: 430px; }
  .card--front .mark-square { left: -160px; }

  .wordmark {
    display: flex; align-items: center; gap: 10px;
    font-weight: 700; color: var(--wordmark-grey);
    letter-spacing: 0.02em;
  }
  .wordmark__square { background: var(--blue); flex: none; }
  .card--back .wordmark {
    position: absolute; left: 36px; bottom: 34px;
    font-size: 46px;
  }
  .card--back .wordmark__square { width: 30px; height: 30px; }

  .front-logo {
    position: absolute; top: 28px; right: 34px;
    font-size: 30px;
  }
  .front-logo .wordmark__square { width: 20px; height: 20px; }

  .contact {
    position: absolute; right: 34px; top: 100px;
    text-align: right; color: var(--text-light);
    font-size: 13.5px; line-height: 1.45;
  }
  .contact__name {
    display: flex; justify-content: flex-end; align-items: center; gap: 8px;
    color: var(--blue); font-weight: 700; font-size: 21px; letter-spacing: 0.03em;
    line-height: 1.2;
  }
  .contact__name-bar { width: 18px; height: 22px; background: var(--blue); }
  .contact__role { font-weight: 600; margin-bottom: 12px; margin-right: 26px; }
  .contact__address { margin-bottom: 14px; margin-right: 26px; }
  .contact__line { display: flex; justify-content: flex-end; align-items: center; gap: 8px; }
  .contact__icon { width: 12px; height: 12px; flex: none; }
</style>
</head>
<body>
<main class="canvas">
  <section class="card card--back">
    <div class="mark-square"></div>
    <div class="wordmark">
      <span class="wordmark__square"></span>
      <span>RTAVENOR</span>
    </div>
  </section>

  <section class="card card--front">
    <div class="mark-square"></div>
    <div class="wordmark front-logo">
      <span class="wordmark__square"></span>
      <span>RTAVENOR</span>
    </div>
    <div class="contact">
      <div class="contact__name"><span>WARREN TAVENOR</span><span class="contact__name-bar"></span></div>
      <div class="contact__role">Founder/President</div>
      <div class="contact__address">4187 Marlowe Ct. Linden Falls,<br>Westmoor County 27614</div>
      <div class="contact__line">
        <span>(640) 555-0147</span>
        <svg class="contact__icon" viewBox="0 0 12 12"><path d="M3 1 L5 3.5 L4 4.8 Q5.5 7 7.2 8 L8.5 7 L11 9 L9.8 11 Q5 10.5 1 3 Z" fill="var(--blue)"/></svg>
      </div>
      <div class="contact__line">
        <span>www.rtavenor.com</span>
        <svg class="contact__icon" viewBox="0 0 12 12"><circle cx="6" cy="6" r="5" fill="none" stroke="var(--blue)" stroke-width="1.4"/><path d="M1 6 H11 M6 1 Q3 6 6 11 M6 1 Q9 6 6 11" fill="none" stroke="var(--blue)" stroke-width="1"/></svg>
      </div>
      <div class="contact__line">
        <span>WRT@RTavenor.com</span>
        <svg class="contact__icon" viewBox="0 0 12 12"><rect x="1" y="2.5" width="10" height="7" fill="none" stroke="var(--blue)" stroke-width="1.4"/><path d="M1 2.5 L6 6.5 L11 2.5" fill="none" stroke="var(--blue)" stroke-width="1.2"/></svg>
      </div>
    </div>
  </section>
</main>
</body>
</html>
```